Update our OBGYN business card look and info

We are an OBGYN office. Our logo is nice but would like to "woman" part of the logo to be a darker color, to contrast with the flower that surrounds it. Maybe make our practice name Bloom Harbor Health more feminine. Our practice caters to women only. All providers and staff are female.

Target Market(s)

Females 16-65.

Industry/Entity Type

Business

Contact Information for Business Card

See attached upload. The ONLY CHANGE to the information is DELETE the name Paula Renwick, Midwife and REPLACE with Dora Fintelli, Midwife

Logo Text

Bloom Harbor Health Obstetrics & Gynecology

Font styles to use
Serif
Script

Colors
85cae6
0692cd
33a6d7
85abd2
f59195
eea4c8
cadf82
fac994
d3a5cc

```html
<!DOCTYPE html>
<html lang="en">
<head>
<meta charset="utf-8">
<title>Bloom Harbor Health – Business Card</title>
<link rel="stylesheet" href="https://fonts.googleapis.com/css2?family=Tinos:wght@400;700&display=swap">
<style>
  :root {
    --stage: #2b2b2d;
    --blue-deep: #0692cd;
    --blue-mid: #33a6d7;
    --blue-light: #85cae6;
    --blue-soft: #4a8fcf;
    --white: #ffffff;
    --brand-blue: #1f8fd0;
  }
  html, body {
    margin: 0;
    padding: 0;
    width: 1200px;
    height: 880px;
    overflow: hidden;
    background: var(--stage);
    font-family: "Tinos", "Times New Roman", serif;
  }
  .canvas {
    position: relative;
    width: 1200px;
    height: 880px;
  }
  .card {
    position: absolute;
    width: 560px;
    height: 320px;
    border-radius: 22px;
    overflow: hidden;
    box-shadow: 0 10px 30px rgba(0,0,0,.45);
  }
  /* Back side */
  .card-back {
    left: 70px;
    top: 80px;
    background: radial-gradient(ellipse at 50% 42%, #5cb7e8 0%, #4a9fdc 40%, var(--blue-soft) 100%);
  }
  .back-brand {
    position: absolute;
    left: 0; right: 0;
    top: 118px;
    display: flex;
    justify-content: center;
    align-items: center;
    gap: 12px;
    color: var(--white);
    font-size: 30px;
  }
  .brand-dot {
    width: 22px; height: 22px;
    border-radius: 50%;
    background: var(--white);
  }
  .back-web {
    position: absolute;
    left: 0; right: 0;
    top: 196px;
    text-align: center;
    color: var(--white);
    font-size: 15px;
    letter-spacing: 2px;
  }
  /* Front side */
  .card-front {
    left: 570px;
    top: 470px;
    background: var(--white);
  }
  .front-wave {
    position: absolute;
    inset: 0;
  }
  .front-brand {
    position: absolute;
    right: 34px;
    top: 40px;
    text-align: right;
    color: var(--brand-blue);
  }
  .front-brand-name {
    display: flex;
    align-items: center;
    justify-content: flex-end;
    gap: 10px;
    font-size: 30px;
  }
  .front-brand-name .brand-dot { background: var(--brand-blue); }
  .front-brand-sub {
    margin-top: 6px;
    font-size: 13px;
    letter-spacing: 1.6px;
    font-weight: 700;
  }
  .providers {
    position: absolute;
    left: 36px;
    top: 150px;
    margin: 0;
    padding: 0;
    list-style: none;
    color: var(--white);
    font-size: 15px;
    line-height: 19px;
  }
  .contacts {
    position: absolute;
    left: 36px;
    top: 256px;
    margin: 0;
    padding: 0;
    list-style: none;
    color: var(--white);
    font-size: 14px;
    line-height: 18px;
  }
  .contacts li { display: flex; align-items: center; gap: 8px; }
  .contacts svg { width: 13px; height: 13px; flex: none; }
  .address {
    position: absolute;
    right: 34px;
    top: 222px;
    text-align: right;
    color: var(--white);
    font-size: 15px;
    line-height: 20px;
    font-style: normal;
  }
</style>
</head>
<body>
<main class="canvas">

  <section class="card card-back" aria-label="Business card back">
    <div class="back-brand"><span class="brand-dot"></span><span>Bloom Harbor Health</span></div>
    <div class="back-web">www.bloomharborhealth.com</div>
  </section>

  <section class="card card-front" aria-label="Business card front">
    <svg class="front-wave" viewBox="0 0 560 320" preserveAspectRatio="none" aria-hidden="true">
      <path d="M0,78 C90,78 150,172 290,174 C400,176 480,140 560,132 L560,320 L0,320 Z" fill="#a9d8ee"/>
      <path d="M0,92 C90,92 150,190 290,190 C400,190 480,158 560,150 L560,320 L0,320 Z" fill="var(--blue-deep)"/>
    </svg>

    <div class="front-brand">
      <div class="front-brand-name"><span class="brand-dot"></span><span>Bloom Harbor Health</span></div>
      <div class="front-brand-sub">OBSTETRICS &amp; GYNECOLOGY</div>
    </div>

    <ul class="providers">
      <li>Marion Kessly, MD</li>
      <li>Tessa Brandow, MD</li>
      <li>Lena Corvath, MD</li>
      <li>Dora Fintelli, Midwife</li>
      <li>Nora Pellham, Midwife</li>
    </ul>

    <ul class="contacts">
      <li>
        <svg viewBox="0 0 14 14"><circle cx="7" cy="7" r="6.3" fill="none" stroke="#fff" stroke-width="1.2"/><rect x="5" y="3.5" width="4" height="7" rx="0.8" fill="none" stroke="#fff" stroke-width="1"/></svg>
        555-310-4826
      </li>
      <li>
        <svg viewBox="0 0 14 14"><circle cx="7" cy="7" r="6.3" fill="none" stroke="#fff" stroke-width="1.2"/><rect x="4" y="5.5" width="6" height="4" fill="none" stroke="#fff" stroke-width="1"/><rect x="5" y="3.5" width="4" height="2" fill="#fff"/></svg>
        555-310-4859
      </li>
      <li>
        <svg viewBox="0 0 14 14"><circle cx="7" cy="7" r="6.3" fill="none" stroke="#fff" stroke-width="1.2"/><circle cx="7" cy="7" r="3.5" fill="none" stroke="#fff" stroke-width="0.9"/><path d="M3.5,7 H10.5 M7,3.5 V10.5" stroke="#fff" stroke-width="0.9"/></svg>
        www.bloomharborhealth.com
      </li>
    </ul>

    <address class="address">
      418 Larkspur Ave, Ste 3B<br>
      Fairhaven, GA 30999-0142
    </address>
  </section>

</main>
</body>
</html>
```